Stationery Design Project

Hi All,

We need you to design stationary for a new Business and Accounting Advisory Firm. We have already got the logo designed and it is attached. If you could also if possible, match the fonts in your design to that on the logo’s provided.

What we need:
- Business Card
- A4 Letter head
- A4 Folders
- PPT template (Title page and regular page)

And what ever else you want to throw in.

We are in the process of getting the web site designed, however below is a list of websites which we like which will give you an understanding of the style that we are going for.

- plivant.example
- moldrabay.example
- tarvenhook.example
- quillorbank.example

I look forward to your seeing your design.
Updates

Hi All,

I have just realised that I forgot that i need to include a Sworn Ledgerkeepers image on the letter head, please find attaced as File 1. Could you please have this image in the bottom left header.

Regards,

Marcus

Industry/Entity Type

Business

Requirements
Must have
• Outputs:
- Documents ready to print
- Generic editable information
- Pdf copies of the documents
- Word version of letterhead

```html
<!DOCTYPE html>
<html lang="en">
<head>
<meta charset="utf-8">
<title>Harrowvale Partners — Stationery</title>
<link rel="stylesheet" href="https://fonts.googleapis.com/css2?family=Arimo:wght@400;700&display=swap">
<style>
  :root {
    --backdrop: #e3e3e3;
    --paper: #ffffff;
    --card: #f3f4f6;
    --brand-blue: #2e4f93;
    --blue-soft: #cfe6f1;
    --blue-softer: #e6f1f7;
    --orange-soft: #fbe0c4;
    --orange-softer: #fdf0e0;
    --orange: #f47b20;
    --ink: #6d6d6d;
    --badge-red: #c8211e;
    --badge-ink: #1c1c1c;
  }
  * { margin: 0; padding: 0; box-sizing: border-box; }
  html, body { width: 1200px; height: 1000px; overflow: hidden; }
  body {
    position: relative;
    background: var(--backdrop);
    font-family: "Arimo", Arial, sans-serif;
    color: var(--ink);
  }

  /* Letterhead */
  .letterhead {
    position: absolute; left: 211px; top: 70px;
    width: 606px; height: 856px;
    background: var(--paper);
    overflow: hidden;
  }

  .accent { position: absolute; }
  .letterhead .accent-warm {
    right: 0; top: 98px; width: 63px; height: 284px;
    background: linear-gradient(to right, var(--orange-softer), var(--orange-soft));
  }
  .letterhead .accent-cool {
    left: 0; top: 516px; width: 65px; height: 282px;
    background: linear-gradient(to left, var(--blue-softer), var(--blue-soft));
  }

  .brand {
    position: absolute;
    display: flex; align-items: center; gap: 8px;
    color: var(--brand-blue);
    font-weight: 400;
    white-space: nowrap;
  }
  .brand-dot { border-radius: 50%; background: var(--orange); flex: none; }
  .letterhead .brand { left: 51px; top: 44px; font-size: 17px; }
  .letterhead .brand-dot { width: 30px; height: 30px; }

  .contact {
    position: absolute;
    font-size: 8.5px; line-height: 11.5px;
    display: grid; grid-template-columns: 14px auto;
    white-space: nowrap;
  }
  .contact .label { color: var(--orange); }
  .contact .address { grid-column: 2; margin-top: 6px; }
  .letterhead .contact { left: 439px; top: 53px; }

  .letterhead .web {
    position: absolute; left: 51px; top: 808px;
    font-size: 10px; color: var(--orange);
  }

  .accreditation {
    position: absolute; left: 433px; top: 776px;
    display: flex; align-items: center; gap: 10px;
  }
  .accreditation-seal {
    width: 44px; height: 44px; border-radius: 50%;
    background: var(--badge-red);
  }
  .accreditation-name {
    font-weight: 700; font-size: 12.5px; line-height: 13px;
    color: var(--badge-ink);
  }

  /* Business cards */
  .card {
    position: absolute; left: 713px; width: 278px;
    background: var(--card);
    overflow: hidden;
  }
  .card-front { top: 499px; height: 139px; border-top-right-radius: 44px; }
  .card-back  { top: 668px; height: 138px; border-top-left-radius: 44px; }

  .card-front .brand { left: 44px; top: 55px; font-size: 15px; }
  .card-front .brand-dot { width: 26px; height: 26px; }

  .card-back .accent-cool {
    right: 0; top: 0; width: 141px; height: 10px;
    background: linear-gradient(to right, var(--blue-softer), var(--blue-soft));
  }
  .card-back .accent-warm {
    left: 0; bottom: 0; width: 156px; height: 10px;
    background: linear-gradient(to right, var(--orange-soft), var(--orange-softer));
  }
  .card-back .web {
    position: absolute; left: 22px; top: 45px;
    font-size: 8.5px; white-space: nowrap;
  }
  .card-back .contact { left: 147px; top: 45px; font-size: 8px; line-height: 12px; }
  .card-back .contact .address { margin-top: 6px; line-height: 11px; }
</style>
</head>
<body>

  <section class="letterhead" aria-label="A4 letterhead">
    <div class="accent accent-warm" role="img" aria-label="Warm orange decorative brand shape"></div>
    <div class="accent accent-cool" role="img" aria-label="Cool blue decorative brand shape"></div>

    <div class="brand"><span class="brand-dot"></span>Harrowvale Partners</div>

    <div class="contact">
      <span class="label">t</span><span>03 000 000</span>
      <span class="label">f</span><span>03 000 000</span>
      <span class="label">m</span><span>0400 000 000</span>
      <span class="label">e</span><span>xxxxx@xxxxxx.com.au</span>
      <span class="address">14 Fernly Street, Oakmere<br>VIC 3000</span>
    </div>

    <div class="web">www.xxxxxxxxxx.com.au</div>

    <div class="accreditation">
      <span class="accreditation-seal"></span>
      <span class="accreditation-name">Sworn<br>Ledgerkeeper</span>
    </div>
  </section>

  <section class="card card-front" aria-label="Business card front">
    <div class="brand"><span class="brand-dot"></span>Harrowvale Partners</div>
  </section>

  <section class="card card-back" aria-label="Business card back">
    <div class="accent accent-cool" role="img" aria-label="Cool blue decorative band"></div>
    <div class="accent accent-warm" role="img" aria-label="Warm orange decorative band"></div>

    <div class="web">www.xxxxxxxx.com.au</div>

    <div class="contact">
      <span class="label">T</span><span>03 000 000</span>
      <span class="label">F</span><span>03 000 000</span>
      <span class="label">M</span><span>0400 000 000</span>
      <span class="label">E</span><span>xxxxx@xxxxxx.com.au</span>
      <span class="address">000 Fernly Street, Oakmere<br>VIC 3000</span>
    </div>
  </section>

</body>
</html>
```